Animal Eye Clinic needs a Business card

We are a new veterinary ophthalmology practice (Ridgeline Pet Vision Care) and we need a business card designed. We only see animal eyes - we are not a regular veterinary clinic. We already have a logo. We are looking for a professional, good looking business card to hand out to our clients. We are looking for something simple but professional and contemporary. Our logo is likely the only picture/graphic that needs to be on the card.
Updates

Contact Information for Business Card

Delia Vossman, BSc, DVM, MSc, DipACVO
Veterinary Ophthalmologist

Phone: 250.418.3927
Email: ridgelinepetvisioncare@mailbox-example.net
Website: ridgelinepetvisioncare-example.net
Address: 1874 Thornbury Rd
Kelowna, BC, V1X 4M9

Colors

Designer to choose colors to be used in the design.

Requirements
Must have
• Our logo (attached)

```html
<!DOCTYPE html>
<html lang="en">
<head>
<meta charset="utf-8">
<title>Ridgeline Pet Vision Care – Business Card</title>
<link rel="stylesheet" href="https://fonts.googleapis.com/css2?family=Roboto:wght@400;500&display=swap">
<style>
  :root {
    --teal: #1b9aa9;
    --ink: #6f7479;
    --ink-strong: #4f5459;
    --card: #ffffff;
    --stage: #d6d8da;
  }
  * { box-sizing: border-box; margin: 0; padding: 0; }
  html, body {
    width: 1200px; height: 930px; overflow: hidden;
    background: var(--stage);
    font-family: "Roboto", Arial, sans-serif;
  }
  .sheet {
    width: 1200px; height: 930px;
    display: flex; flex-direction: column;
    align-items: center; justify-content: center; gap: 50px;
  }
  .card {
    width: 700px; height: 400px;
    background: var(--card);
    border-radius: 28px;
    box-shadow: 0 6px 18px rgba(0,0,0,.18);
    position: relative;
  }
  /* front */
  .card-front {
    display: flex; align-items: center; justify-content: center;
  }
  .brand {
    display: flex; align-items: center; gap: 16px;
    color: var(--teal);
    font-weight: 500; font-size: 34px; letter-spacing: .5px;
  }
  .brand-dot {
    width: 46px; height: 46px; border-radius: 50%;
    background: var(--teal);
  }
  /* back */
  .person {
    position: absolute; left: 56px; bottom: 70px;
  }
  .person-name {
    color: var(--teal); font-size: 38px; font-weight: 400; line-height: 1.1;
  }
  .person-role {
    color: var(--ink); font-size: 17px; line-height: 1.4; margin-top: 6px;
  }
  .contact {
    position: absolute; left: 330px; top: 110px;
    color: var(--ink); font-size: 16px; line-height: 1.45;
  }
  .contact-address { margin-bottom: 10px; }
  .contact-row { display: flex; align-items: center; gap: 10px; }
  .contact-row svg { width: 14px; height: 14px; flex: none; }
  .contact-row strong { color: var(--ink-strong); font-weight: 500; }
</style>
</head>
<body>
<main class="sheet">
  <section class="card card-front">
    <div class="brand">
      <span class="brand-dot"></span>
      <span class="brand-name">Ridgeline Pet Vision Care</span>
    </div>
  </section>

  <section class="card card-back">
    <div class="person">
      <h1 class="person-name">Delia Vossman</h1>
      <p class="person-role">BSc, DVM, MSc, DipACVO<br>Veterinary Ophthalmologist</p>
    </div>
    <div class="contact">
      <p class="contact-address">Address: 1874 Thornbury Rd<br>Kelowna, BC, V1X 4M9</p>
      <p class="contact-row">
        <svg viewBox="0 0 16 16" aria-hidden="true"><path d="M3 1.5l3 .5 1 3.5-2 1.2a8 8 0 0 0 4.3 4.3L10.5 9l3.5 1 .5 3-2 1.5C7 14 2 9 1.5 3.5z" fill="var(--teal)"/></svg>
        250.418.3927
      </p>
      <p class="contact-row">
        <svg viewBox="0 0 16 16" aria-hidden="true"><rect x="1.5" y="3.5" width="13" height="9" fill="none" stroke="var(--teal)" stroke-width="1.5"/><path d="M1.5 3.5l6.5 5 6.5-5" fill="none" stroke="var(--teal)" stroke-width="1.5"/></svg>
        ridgelinepetvisioncare@mailbox-example.net
      </p>
      <p class="contact-row">
        <svg viewBox="0 0 16 16" aria-hidden="true"><circle cx="8" cy="8" r="6.5" fill="none" stroke="var(--teal)" stroke-width="1.5"/><ellipse cx="8" cy="8" rx="2.8" ry="6.5" fill="none" stroke="var(--teal)" stroke-width="1.2"/><path d="M1.5 8h13" stroke="var(--teal)" stroke-width="1.2"/></svg>
        <span>www.<strong>ridgelinepetvisioncare</strong>-example.net</span>
      </p>
    </div>
  </section>
</main>
</body>
</html>
```